Four in One (Flexible infographic for Content Management Industry)

See attachment.
A graphic depicting 4 products, where each can stand on its own and each can be combined with others, but where, if all are taken together, the best result is achieved (the "super product").
Intended use is web. See attached file as an example.
The most basic idea is as the attached diagram shows, where 4 rectangles are arranged in a quadrangle, with a middle rectangle in the center representing the combined 4 products. This concept is fine except it is a bit too obvious as it stands. We are looking for either a variation of this or another concept.
The audience is technical + professional + enterprise - NOT consumers. Hence the design should be conservative in nature.
We are aware of tools like as Canva or Pictogram where such graphics are available, but we are looking for something with a bit more imagination and flexibility.
This graphic should be targeted to web sites and be delivered with vector-based (SVG) graphics.

```html
<!DOCTYPE html>
<html lang="en">
<head>
<meta charset="utf-8">
<title>Super Product – Four in One</title>
<link rel="stylesheet" href="https://fonts.googleapis.com/css2?family=Montserrat:wght@600;700;800&display=swap">
<style>
  :root {
    --bg: #ffffff;
    --frame: #9a9a9b;
    --doc-management: #3d4f63;
    --security: #52a9b1;
    --erp: #51658c;
    --digital: #3a7480;
    --tab-accent: #b8cfdc;
    --title: #464646;
    --on-petal: #ffffff;
  }
  html, body {
    margin: 0;
    padding: 0;
    width: 1200px;
    height: 982px;
    overflow: hidden;
    background: var(--bg);
  }
  .infographic {
    display: block;
    width: 1200px;
    height: 982px;
    font-family: "Montserrat", Arial, sans-serif;
  }
  .frame { fill: var(--bg); stroke: var(--frame); stroke-width: 8; }
  .petal--documents { fill: var(--doc-management); }
  .petal--security { fill: var(--security); }
  .petal--erp { fill: var(--erp); }
  .petal--digital { fill: var(--digital); }
  .petal-rim { fill: none; stroke: var(--on-petal); stroke-width: 3; }
  .icon-tab { fill: var(--bg); }
  .tab-fold { fill: var(--tab-accent); }
  .hub { fill: var(--bg); }
  .hub-title { fill: var(--title); font-size: 96px; font-weight: 800; }
  .petal-heading { fill: var(--on-petal); font-size: 37px; font-weight: 700; }
  .petal-heading--small { font-size: 33px; }
  .heading-rule { stroke: var(--on-petal); stroke-width: 3; }
  .petal-summary { fill: var(--on-petal); font-size: 19.5px; font-weight: 700; }
  .petal-summary--bold { font-weight: 800; }
  .feature { fill: var(--on-petal); font-size: 19.5px; font-weight: 600; }
  .tick { fill: none; stroke: var(--on-petal); stroke-width: 3.2; stroke-linecap: round; stroke-linejoin: round; }
  .icon-line { fill: none; stroke-width: 4.5; stroke-linecap: round; stroke-linejoin: round; }
</style>
</head>
<body>
<svg class="infographic" viewBox="0 0 2122 1736" xmlns="http://www.w3.org/2000/svg" role="img" aria-label="Super Product: four combinable products">
  <defs>
    <path id="petal-shape" d="M388,195 H730 A297,297 0 0 1 1027,492 V840 H720 A332,332 0 0 1 388,508 Z"/>
    <path id="petal-rim" d="M415,220 H730 A270,270 0 0 1 1000,492 V830 H720 A305,305 0 0 1 415,508 Z"/>
    <g id="icon-tab">
      <polygon class="tab-fold" points="328,402 389,402 389,438"/>
      <path class="icon-tab" d="M328,258 H558 A80,80 0 0 1 638,338 V402 H328 Z"/>
    </g>
    <path id="tick" class="tick" d="M-7,0 L-2,5 L7,-5"/>
  </defs>

  <path class="frame" d="M345,152 H735 C900,152 1020,260 1062,405 C1105,260 1225,152 1385,152 H1780 V213 H1837 V445 L1775,478 V560 C1775,700 1680,810 1530,868 C1680,925 1775,1035 1775,1190 V1270 L1837,1305 V1535 H1780 V1585 H1385 C1225,1585 1105,1480 1062,1330 C1020,1480 900,1585 735,1585 H345 V1535 H285 V1305 L350,1270 V1190 C350,1035 445,925 595,868 C445,810 350,700 350,560 V478 L285,445 V213 H345 Z"/>

  <g class="quadrant quadrant--documents">
    <use href="#petal-shape" class="petal--documents"/>
    <use href="#petal-rim" class="petal-rim"/>
    <use href="#icon-tab"/>
  </g>
  <g class="quadrant quadrant--security" transform="matrix(-1 0 0 1 2125 0)">
    <use href="#petal-shape" class="petal--security"/>
    <use href="#petal-rim" class="petal-rim"/>
    <use href="#icon-tab"/>
  </g>
  <g class="quadrant quadrant--erp" transform="matrix(1 0 0 -1 0 1735)">
    <use href="#petal-shape" class="petal--erp"/>
    <use href="#petal-rim" class="petal-rim"/>
    <use href="#icon-tab"/>
  </g>
  <g class="quadrant quadrant--digital" transform="matrix(-1 0 0 -1 2125 1735)">
    <use href="#petal-shape" class="petal--digital"/>
    <use href="#petal-rim" class="petal-rim"/>
    <use href="#icon-tab"/>
  </g>

  <rect class="hub" x="650" y="775" width="826" height="174" rx="86"/>
  <text class="hub-title" x="706" y="895" textLength="704" lengthAdjust="spacingAndGlyphs">Super Product</text>

  <g class="icon icon--document" stroke="var(--doc-management)">
    <path class="icon-line" d="M503,281 H555 L570,296 V370 H503 Z M555,281 V296 H570"/>
    <path class="icon-line" d="M515,303 H552 M515,318 H558 M515,331 H558 M515,344 H558" stroke-width="3.5"/>
  </g>
  <g class="icon icon--shield" stroke="var(--security)">
    <path class="icon-line" d="M1585,280 L1626,296 V330 C1626,352 1608,368 1585,379 C1562,368 1544,352 1544,330 V296 Z"/>
    <circle cx="1585" cy="330" r="22" fill="var(--security)" stroke="none"/>
    <path class="icon-line" d="M1574,330 L1582,338 L1597,322" stroke="#fff"/>
  </g>
  <g class="icon icon--documents" stroke="var(--erp)">
    <path class="icon-line" d="M503,1387 H578 V1472 H503 Z" stroke-width="4"/>
    <path class="icon-line" d="M493,1375 H566 V1460 H493 Z" fill="#fff"/>
    <path class="icon-line" d="M518,1393 H560 M505,1408 H560 M505,1423 H560 M505,1438 H560" stroke-width="4"/>
  </g>
  <g class="icon icon--signal" stroke="var(--digital)">
    <path class="icon-line" d="M1530,1398 C1557,1372 1595,1372 1622,1398" stroke-width="9"/>
    <path class="icon-line" d="M1546,1414 C1564,1397 1588,1397 1606,1414" stroke-width="9"/>
    <circle cx="1576" cy="1446" r="12" fill="var(--digital)" stroke="none"/>
  </g>

  <g class="content content--documents">
    <text class="petal-heading" x="468" y="464" textLength="484" lengthAdjust="spacingAndGlyphs">Document Management</text>
    <line class="heading-rule" x1="475" y1="487" x2="960" y2="487"/>
    <text class="petal-summary" x="494" y="532" textLength="481" lengthAdjust="spacingAndGlyphs">Streamline document organization, access, and</text>
    <text class="petal-summary" x="471" y="556" textLength="504" lengthAdjust="spacingAndGlyphs">collaboration with easier file storage and sharing,</text>
    <text class="petal-summary" x="601" y="581" textLength="374" lengthAdjust="spacingAndGlyphs">leading to more efficient workflows .</text>
    <use href="#tick" x="545" y="644"/><text class="feature" x="562" y="650" textLength="310" lengthAdjust="spacingAndGlyphs">Centralized Document Control</text>
    <use href="#tick" x="545" y="669"/><text class="feature" x="562" y="675" textLength="375" lengthAdjust="spacingAndGlyphs">Collaborative Workspace Integration</text>
    <use href="#tick" x="545" y="693"/><text class="feature" x="562" y="700" textLength="334" lengthAdjust="spacingAndGlyphs">Automated Compliance Tracking</text>
    <use href="#tick" x="545" y="718"/><text class="feature" x="562" y="724" textLength="82" lengthAdjust="spacingAndGlyphs">Check 4</text>
  </g>

  <g class="content content--security">
    <text class="petal-heading" x="1158" y="464" textLength="509" lengthAdjust="spacingAndGlyphs">Security and Compliance</text>
    <line class="heading-rule" x1="1163" y1="487" x2="1667" y2="487"/>
    <text class="petal-summary petal-summary--bold" x="1160" y="532" textLength="505" lengthAdjust="spacingAndGlyphs">Benefit from tailored cloud solutions, secure data</text>
    <text class="petal-summary petal-summary--bold" x="1160" y="556" textLength="509" lengthAdjust="spacingAndGlyphs">storage, and expert disaster recovery planning for</text>
    <text class="petal-summary petal-summary--bold" x="1160" y="581" textLength="357" lengthAdjust="spacingAndGlyphs">reliable and scalable IT operations.</text>
    <use href="#tick" x="1177" y="644"/><text class="feature" x="1207" y="650" textLength="245" lengthAdjust="spacingAndGlyphs">Custom Cloud Solutions</text>
    <use href="#tick" x="1177" y="669"/><text class="feature" x="1207" y="675" textLength="209" lengthAdjust="spacingAndGlyphs">Secure Data Storage</text>
    <use href="#tick" x="1177" y="693"/><text class="feature" x="1207" y="700" textLength="257" lengthAdjust="spacingAndGlyphs">Expert Disaster Recovery</text>
    <use href="#tick" x="1177" y="718"/><text class="feature" x="1207" y="724" textLength="82" lengthAdjust="spacingAndGlyphs">Check 4</text>
  </g>

  <g class="content content--erp">
    <text class="petal-heading petal-heading--small" x="495" y="1052" textLength="483" lengthAdjust="spacingAndGlyphs">Enterprise Resource Planning</text>
    <line class="heading-rule" x1="500" y1="1074" x2="970" y2="1074"/>
    <text class="petal-summary" x="487" y="1117" textLength="485" lengthAdjust="spacingAndGlyphs">Simplify management across finance, sales, and</text>
    <text class="petal-summary" x="519" y="1141" textLength="453" lengthAdjust="spacingAndGlyphs">operations, enabling better decision-making</text>
    <text class="petal-summary" x="696" y="1166" textLength="276" lengthAdjust="spacingAndGlyphs">and improved productivity.</text>
    <use href="#tick" x="521" y="1231"/><text class="feature" x="543" y="1237" textLength="306" lengthAdjust="spacingAndGlyphs">Integrated Business Processes</text>
    <use href="#tick" x="521" y="1256"/><text class="feature" x="543" y="1262" textLength="275" lengthAdjust="spacingAndGlyphs">Enhanced Decision-Making</text>
    <use href="#tick" x="521" y="1280"/><text class="feature" x="543" y="1286" textLength="266" lengthAdjust="spacingAndGlyphs">Productivity Improvement</text>
    <use href="#tick" x="521" y="1305"/><text class="feature" x="543" y="1311" textLength="82" lengthAdjust="spacingAndGlyphs">Check 4</text>
  </g>

  <g class="content content--digital">
    <text class="petal-heading petal-heading--small" x="1158" y="1052" textLength="402" lengthAdjust="spacingAndGlyphs">Digital Transformation</text>
    <line class="heading-rule" x1="1163" y1="1074" x2="1635" y2="1074"/>
    <text class="petal-summary" x="1160" y="1119" textLength="482" lengthAdjust="spacingAndGlyphs">Turn scanned documents into easily searchable</text>
    <text class="petal-summary" x="1160" y="1143" textLength="408" lengthAdjust="spacingAndGlyphs">digital archives, boosting efficiency and</text>
    <text class="petal-summary" x="1160" y="1168" textLength="129" lengthAdjust="spacingAndGlyphs">accessibility.</text>
    <use href="#tick" x="1177" y="1231"/><text class="feature" x="1207" y="1237" textLength="382" lengthAdjust="spacingAndGlyphs">Instant searchable Archives with OCR</text>
    <use href="#tick" x="1177" y="1256"/><text class="feature" x="1207" y="1262" textLength="368" lengthAdjust="spacingAndGlyphs">Automated Document Classification</text>
    <use href="#tick" x="1177" y="1280"/><text class="feature" x="1207" y="1286" textLength="340" lengthAdjust="spacingAndGlyphs">TeamPortal and Cloud Blob Ready</text>
    <use href="#tick" x="1177" y="1305"/><text class="feature" x="1207" y="1311" textLength="82" lengthAdjust="spacingAndGlyphs">Check 4</text>
  </g>
</svg>
</body>
</html>
```